Canadian Christian Church needs design for new sermon series

A graphic design for our series and an invitation card to invite people to the series. Check design brief for more detailed information. Target audience: young families and young adults. Looking for a creative design that will get people's attention and create interest. See design brief for copy of design purchased for previous series.
Updates
entered Apr 4 incorrectly. Need a week to receive and review designs, and today is Apr 2/19. Thanks!
Target Market(s)
young families and young adults
Colors
Designer to choose colors to be used in the design.
Look and feel

```html
<!DOCTYPE html>
<html lang="en">
<head>
<meta charset="utf-8">
<title>Messy – Series Card Options</title>
<link rel="stylesheet" href="https://fonts.googleapis.com/css2?family=Rubik+Scribble&family=Rubik+Dirt&family=Rubik+Distressed&family=Fredericka+the+Great&family=Merriweather:wght@700&family=Oswald:wght@300&family=Noto+Serif:wght@400&display=swap">
<style>
  :root {
    --board: #b3a797;
    --card: #57454f;
    --card-light: #7a6870;
    --band: #3e2c3a;
    --band-edge: #4b3a47;
    --ink: #ffffff;
    --number: #1a1614;
    --mark: #e59a3a;
  }
  * { margin: 0; padding: 0; box-sizing: border-box; }
  html, body { width: 1200px; height: 934px; overflow: hidden; }
  body { background: var(--board); position: relative; }

  .option-number {
    position: absolute;
    font-family: "Noto Serif", "Times New Roman", serif;
    font-size: 122px;
    line-height: 1;
    color: var(--number);
  }

  .card {
    position: absolute;
    width: 464px;
    height: 364px;
    background:
      radial-gradient(ellipse at 30% 20%, var(--card-light) 0%, transparent 55%),
      radial-gradient(ellipse at 80% 70%, #6a5862 0%, transparent 50%),
      var(--card);
    overflow: hidden;
  }

  .church-mark {
    position: absolute;
    right: 24px;
    top: 30px;
    width: 170px;
    text-align: center;
  }
  .church-mark .dot {
    display: block;
    width: 52px;
    height: 52px;
    margin: 0 auto 6px 83px;
    border-radius: 50%;
    background: var(--mark);
  }
  .church-mark .name {
    font-family: "Oswald", Arial, sans-serif;
    font-weight: 300;
    font-size: 11px;
    color: var(--ink);
    white-space: nowrap;
    display: block;
    text-align: right;
  }

  .series-title {
    position: absolute;
    left: 0;
    right: 0;
    top: 118px;
    text-align: center;
    color: var(--ink);
    font-size: 118px;
    line-height: 1;
    letter-spacing: 2px;
  }
  .title-scribble { font-family: "Rubik Scribble", sans-serif; }
  .title-dirt { font-family: "Rubik Dirt", sans-serif; }
  .title-outline { font-family: "Fredericka the Great", serif; font-size: 112px; }
  .title-distressed { font-family: "Rubik Distressed", sans-serif; }

  .tagline-band {
    position: absolute;
    left: 0;
    right: 0;
    top: 291px;
    height: 60px;
    background: var(--band);
    display: flex;
    align-items: center;
    justify-content: center;
  }
  .tagline-band::after {
    content: "";
    position: absolute;
    left: 0; right: 0; top: 60px; height: 13px;
    background: var(--band-edge);
  }
  .tagline {
    font-family: "Merriweather", Georgia, serif;
    font-weight: 700;
    font-size: 30px;
    color: var(--ink);
  }
</style>
</head>
<body>
  <span class="option-number" style="left:38px;top:80px;">1</span>
  <span class="option-number" style="left:602px;top:80px;">2</span>
  <span class="option-number" style="left:20px;top:486px;">3</span>
  <span class="option-number" style="left:596px;top:486px;">4</span>

  <section class="card" style="left:106px;top:82px;">
    <div class="church-mark"><span class="dot"></span><span class="name">Maple Grove Family Church</span></div>
    <h1 class="series-title title-scribble">MESSY</h1>
    <div class="tagline-band"><p class="tagline">Joining God in the Mess</p></div>
  </section>

  <section class="card" style="left:690px;top:82px;">
    <div class="church-mark"><span class="dot"></span><span class="name">Maple Grove Family Church</span></div>
    <h1 class="series-title title-dirt">MESSY</h1>
    <div class="tagline-band"><p class="tagline">Joining God in the Mess</p></div>
  </section>

  <section class="card" style="left:106px;top:486px;">
    <div class="church-mark"><span class="dot"></span><span class="name">Maple Grove Family Church</span></div>
    <h1 class="series-title title-outline">MESSY</h1>
    <div class="tagline-band"><p class="tagline">Joining God in the Mess</p></div>
  </section>

  <section class="card" style="left:690px;top:486px;">
    <div class="church-mark"><span class="dot"></span><span class="name">Maple Grove Family Church</span></div>
    <h1 class="series-title title-distressed">MESSY</h1>
    <div class="tagline-band"><p class="tagline">Joining God in the Mess</p></div>
  </section>
</body>
</html>
```